Professional violinist needs business cards

I am trying to attract the following jobs:
-private violin lessons (primarily classical)
-performance gigs (weddings, birthday parties, funerals, etc.)
-collaborations with other artists (studio recordings, performances)

I want to communicate that I have a very high standard of excellence for my work, but I also love people and celebrations.
Values/style words I like are:
love, joy, peace, fun, beauty, authenticity, excellence, warmth, refined/sleek, free spirited. If that's too confusing, just ignore :)

I will attach my favorite business card template that I could find on Canva. The lines are supposed to be like a music staff, which I think is really cool, but I also don't want it to look too busy. I like the simple black and white--I think it looks sharp--but I also am open to other ideas. I also have seen business cards with pictures included that looked great, so I attached an image that could be used as well.

I am also attaching a file that I made of my initials that could be used as a logo, but I'm not sure if it should be included.

Information on the card:
-My name (18 letters total)
-"violinist"
-phone number, email, website

Thank you!

```html
<!DOCTYPE html>
<html lang="en">
<head>
<meta charset="UTF-8">
<title>Elena Marwick – Violinist Business Card</title>
<link href="https://fonts.googleapis.com/css2?family=Dancing+Script:wght@500&family=Cinzel:wght@500&family=Crimson+Text:wght@400&display=swap" rel="stylesheet">
<style>
  :root {
    --backdrop: #2b2b2c;
    --card: #1f2327;
    --gold: #c9b089;
    --gold-dark: #a88d62;
    --ink-light: #ece9e4;
    --silver-light: #f1f1f1;
    --silver-dark: #c9c9cb;
    --photo-top: #7d7466;
    --photo-bottom: #3c3935;
  }
  * { margin: 0; padding: 0; box-sizing: border-box; }
  html, body {
    width: 1200px; height: 1138px; overflow: hidden;
    background: var(--backdrop);
  }
  .card {
    position: absolute;
    left: 276px;
    width: 620px;
    height: 374px;
    background: var(--card);
    border-radius: 12px;
    overflow: hidden;
  }
  .card--front { top: 186px; }
  .card--back { top: 608px; }

  /* Front */
  .clef-art {
    position: absolute; left: 0; top: 0;
    width: 142px; height: 100%;
    background: linear-gradient(160deg, var(--silver-light), var(--silver-dark));
    opacity: 0.18;
  }
  .brand-mark {
    position: absolute;
    left: 349px; top: 112px;
    width: 56px; height: 56px;
    border: 2px solid var(--gold);
    border-radius: 50%;
  }
  .front-title {
    position: absolute;
    left: 218px; width: 332px;
    top: 196px;
    text-align: center;
  }
  .front-title .name {
    font-family: 'Dancing Script', cursive;
    font-weight: 500;
    font-size: 38px;
    color: var(--ink-light);
    line-height: 1;
  }
  .role {
    display: flex; align-items: center; justify-content: center;
    font-family: 'Cinzel', serif;
    color: var(--ink-light);
    letter-spacing: 0.18em;
  }
  .role::before, .role::after {
    content: ""; height: 1px; flex: 1;
    background: var(--gold);
  }
  .front-title .role { font-size: 17px; margin-top: 12px; }
  .front-title .role span { padding: 0 20px 0 24px; }

  /* Back */
  .back-mark {
    position: absolute; left: 36px; top: 62px;
    width: 46px; height: 46px;
    border: 2px solid var(--gold);
    border-radius: 50%;
  }
  .back-brand {
    position: absolute; left: 101px; top: 62px; width: 194px;
    text-align: center;
  }
  .back-brand .name {
    font-family: 'Dancing Script', cursive;
    font-weight: 500;
    font-size: 22px;
    color: var(--ink-light);
    line-height: 1;
  }
  .back-brand .role { font-size: 10px; margin-top: 6px; }
  .back-brand .role span { padding: 0 10px 0 12px; }

  .contact-name {
    position: absolute; left: 31px; top: 196px;
    font-family: 'Dancing Script', cursive;
    font-weight: 500;
    font-size: 22px;
    color: var(--ink-light);
  }
  .contact-list {
    position: absolute; left: 31px; top: 240px;
    list-style: none;
    font-family: 'Crimson Text', serif;
    font-size: 15px;
    color: var(--ink-light);
  }
  .contact-list li {
    display: flex; align-items: center;
    height: 23.3px;
  }
  .contact-list svg {
    width: 13px; height: 13px; margin-right: 15px;
    fill: var(--ink-light);
  }
  .contact-list .accent { color: var(--gold); }

  .photo-panel {
    position: absolute; left: 0; top: 0;
    width: 620px; height: 374px;
  }
</style>
</head>
<body>

<section class="card card--front">
  <div class="clef-art" role="img" aria-label="Large silver treble clef along the left edge"></div>
  <div class="brand-mark"></div>
  <div class="front-title">
    <div class="name">Elena Marwick</div>
    <div class="role"><span>VIOLINIST</span></div>
  </div>
</section>

<section class="card card--back">
  <div class="back-mark"></div>
  <div class="back-brand">
    <div class="name">Elena Marwick</div>
    <div class="role"><span>VIOLINIST</span></div>
  </div>

  <div class="contact-name">Elena Marwick</div>
  <ul class="contact-list">
    <li>
      <svg viewBox="0 0 16 16"><path d="M3 5c0-2 2-3 5-3s5 1 5 3l-1 1.5-2.5-.5V4.5h-3V6L4 6.5zM4 8h8l1 6H3z"/></svg>
      +1 (202) 555-0147
    </li>
    <li>
      <svg viewBox="0 0 16 16"><path d="M8 1a5 5 0 0 0-5 5c0 4 5 9 5 9s5-5 5-9a5 5 0 0 0-5-5zm0 7a2 2 0 1 1 0-4 2 2 0 0 1 0 4z"/></svg>
      Fairhaven, VA
    </li>
    <li>
      <svg viewBox="0 0 16 16"><path d="M8 1a7 7 0 1 0 0 14A7 7 0 0 0 8 1zm0 1.5c.8 0 1.7 1.6 2 4H6c.3-2.4 1.2-4 2-4zM2.6 7.3h2.6c0 .9.1 1.5.2 1.5H2.6a5.6 5.6 0 0 1 0-1.5zm3.4 0h4c0 .5 0 1-.1 1.5H6.1L6 7.3zm4.8 0h2.6a5.6 5.6 0 0 1 0 1.5h-2.7l.1-1.5zM6 9.6h4c-.3 2.4-1.2 4-2 4s-1.7-1.6-2-4z"/></svg>
      <span>www.<span class="accent">ElenaMarwick</span>.com</span>
    </li>
    <li>
      <svg viewBox="0 0 16 16"><path d="M1 3h14v10H1zm1.5 1.5v.3L8 9l5.5-4.2v-.3zm0 2.1v5h11v-5L8 10.8z"/></svg>
      Elena@ElenaMarwick.com
    </li>
  </ul>

  <svg class="photo-panel" viewBox="0 0 620 374" aria-hidden="false">
    <defs>
      <linearGradient id="goldBand" x1="0" y1="0" x2="0" y2="1">
        <stop offset="0" stop-color="var(--gold)"/>
        <stop offset="1" stop-color="var(--gold-dark)"/>
      </linearGradient>
      <linearGradient id="photoTone" x1="0" y1="0" x2="0" y2="1">
        <stop offset="0" stop-color="#7d7466"/>
        <stop offset="1" stop-color="#3c3935"/>
      </linearGradient>
    </defs>
    <path d="M392 0 Q283 190 403 374 L407 374 Q300 190 407 0 Z" fill="url(#goldBand)"/>
    <path d="M407 0 Q300 190 403 374 L620 374 L620 0 Z" fill="url(#photoTone)" role="img" aria-label="Photo of the violinist in a black dress holding her violin beside a stone wall"/>
  </svg>
</section>

</body>
</html>
```